Plakat-Design für IT-Systemhaus
The winner of our first design contests on this site. Can only say positive things about them. They work fast, respond in a timely manner and created a great design for us. Overall we're very happy with Quindrel.
Zielgruppe
Wir sind ein IT-Systemhaus mit dem Fokus auf individuelle Cloud Lösungen inkl. bester Kundenbetreuung.
Unsere primäre Zielgruppe sind Unterhnemenskunden, sprich das B2B Geschäft.
Aus der Gruppe der Unternehmenskunden interessieren uns besonders kleine und mittelständische Unternehmen.
Unser Corporate Design ist modern und dennoch auffällig gehalten.
Unsere bevorzugt Schriftart ist 'Ubuntu' bzw. 'Ubuntu Light'.
Unsere Grundfarben sind Orange (#ff8303) Grau (#747474).
Als orientierungshilfe haben wir unser Vorlage für Blöcke und Flyer mit angehangen.
Aufgabenstellung
Es handelt sich um eine Geländerwerbung (doppelseitig) zwischen einer Tankstelle und einer Straße gelegen. (Siehe Anhang)
Die Maße des Anzeitgetafel sind wie folgt: Querformat 135 x 65 (breite x höhe)
Gerne würden wir auf eine etwas provokantere Fragestellung zurückgreifen, um Aufmerksamkeit zu eregen.
Gleichzeitig möchten wir als Lösungsfinder der Fragestellung wargenommen werden.
Gut gefallen hat uns diese Lösung: https://www.grafikvorhof.at/529071-plakat-fuer-it-systemhaus
Des Weiteren sollte die Anzeige unser Logo, Webadresse sowie unsere Telefonnummer enthalten.
Für Kreative Vorschläge sind wir dankbar.

```html
<!DOCTYPE html>
<html lang="de">
<head>
<meta charset="utf-8">
<title>Kemo IT Solutions – Bannerwerbung</title>
<link rel="stylesheet" href="https://fonts.googleapis.com/css2?family=Ubuntu:wght@300;400;500;700&display=swap">
<style>
  :root {
    --orange: #e8832f;
    --white: #f4f4f4;
    --grey-bg: #d9d9d9;
    --photo-light: #e6e6e6;
    --photo-mid: #b9a48c;
    --photo-dark: #6d5f55;
  }
  html, body {
    margin: 0;
    padding: 0;
    width: 857px;
    height: 1200px;
    overflow: hidden;
    background: var(--grey-bg);
    font-family: "Ubuntu", sans-serif;
  }
  .banner {
    position: absolute;
    left: 113px;
    width: 652px;
    height: 325px;
    display: block;
    box-shadow: 0 2px 6px rgba(0,0,0,0.15);
  }
  .banner--orange { top: 139px; }
  .banner--white { top: 721px; }
  .headline { font-family: "Ubuntu", sans-serif; font-weight: 700; font-size: 34px; }
  .tagline { font-family: "Ubuntu", sans-serif; font-weight: 700; font-size: 25px; }
  .brand-name { font-family: "Ubuntu", sans-serif; font-weight: 700; font-size: 17px; }
  .service-label { font-family: "Ubuntu", sans-serif; font-weight: 700; font-size: 14.5px; fill: var(--white); }
  .contact { font-family: "Ubuntu", sans-serif; font-weight: 700; font-size: 16px; }
</style>
</head>
<body>

<!-- Banner variant: orange -->
<svg class="banner banner--orange" viewBox="0 0 652 325" xmlns="http://www.w3.org/2000/svg">
  <defs>
    <linearGradient id="photoToneA" x1="0" y1="0" x2="1" y2="1">
      <stop offset="0" stop-color="#e6e6e6"/>
      <stop offset="0.55" stop-color="#b9a48c"/>
      <stop offset="1" stop-color="#6d5f55"/>
    </linearGradient>
    <linearGradient id="orangeFade" x1="0" y1="0" x2="1" y2="0">
      <stop offset="0" stop-color="#e6802c"/>
      <stop offset="0.3" stop-color="#ec9449"/>
      <stop offset="0.42" stop-color="#f1b07a" stop-opacity="0.85"/>
      <stop offset="0.62" stop-color="#f4f4f4" stop-opacity="0"/>
    </linearGradient>
  </defs>
  <rect class="canvas-bg" width="652" height="325" fill="var(--photo-light)"/>
  <rect class="photo-area" x="240" y="0" width="412" height="325" fill="url(#photoToneA)" role="img" aria-label="Foto: wütender Mann im karierten Hemd holt mit einem Hammer über seinem Laptop aus"/>
  <rect class="orange-fade" width="652" height="240" fill="url(#orangeFade)"/>

  <text class="headline" fill="var(--white)" x="31" y="61">Haben Sie Ihre</text>
  <text class="headline" fill="var(--white)" x="31" y="104">IT im Griff?</text>
  <text class="tagline" fill="var(--white)" x="31" y="175">it gemeinsam</text>
  <text class="tagline" fill="var(--white)" x="31" y="205">optimieren.</text>

  <polygon class="bottom-strip" points="190,317 652,317 652,325 195,325" fill="var(--orange)"/>
  <polygon class="logo-panel" points="0,240 180,240 195,325 0,325" fill="var(--white)"/>
  <text class="brand-name" fill="var(--orange)" x="90" y="288" text-anchor="middle">Kemo IT Solutions</text>

  <g class="services">
    <polygon points="194,248 292,248 296,278 198,278" fill="var(--orange)"/>
    <text class="service-label" x="245" y="268" text-anchor="middle">IT Beratung</text>
    <polygon points="298,248 403,248 407,278 302,278" fill="var(--orange)"/>
    <text class="service-label" x="352" y="268" text-anchor="middle">IT Sicherheit</text>
    <polygon points="409,248 502,248 506,278 413,278" fill="var(--orange)"/>
    <text class="service-label" x="457" y="268" text-anchor="middle">IT Support</text>
    <polygon points="508,248 632,248 636,278 512,278" fill="var(--orange)"/>
    <text class="service-label" x="572" y="268" text-anchor="middle">IT Infrastruktur</text>
  </g>

  <polygon class="phone-bar" points="200,285 460,285 463,317 205,317" fill="var(--white)"/>
  <text class="contact" fill="var(--orange)" x="333" y="307" text-anchor="middle">Tel : +49 2351 / 38 72 14 0</text>
  <polygon class="web-bar" points="457,285 640,285 636,317 462,317" fill="var(--orange)"/>
  <text class="contact" fill="var(--white)" x="549" y="307" text-anchor="middle">www.kemo-it.de</text>
</svg>

<!-- Banner variant: white -->
<svg class="banner banner--white" viewBox="0 0 652 325" xmlns="http://www.w3.org/2000/svg">
  <defs>
    <linearGradient id="photoToneB" x1="0" y1="0" x2="1" y2="1">
      <stop offset="0" stop-color="#e6e6e6"/>
      <stop offset="0.55" stop-color="#b9a48c"/>
      <stop offset="1" stop-color="#6d5f55"/>
    </linearGradient>
    <linearGradient id="whiteFade" x1="0" y1="0" x2="1" y2="0">
      <stop offset="0" stop-color="#f4f4f4"/>
      <stop offset="0.35" stop-color="#f4f4f4"/>
      <stop offset="0.62" stop-color="#f4f4f4" stop-opacity="0"/>
    </linearGradient>
  </defs>
  <rect class="canvas-bg" width="652" height="325" fill="var(--photo-light)"/>
  <rect class="photo-area" x="240" y="0" width="412" height="325" fill="url(#photoToneB)" role="img" aria-label="Foto: wütender Mann im karierten Hemd holt mit einem Hammer über seinem Laptop aus"/>
  <rect class="white-fade" width="652" height="240" fill="url(#whiteFade)"/>

  <text class="headline" fill="var(--orange)" x="31" y="61">Haben Sie Ihre</text>
  <text class="headline" fill="var(--orange)" x="31" y="104">IT im Griff?</text>
  <text class="tagline" fill="var(--orange)" x="31" y="175">it gemeinsam</text>
  <text class="tagline" fill="var(--orange)" x="31" y="205">optimieren.</text>

  <polygon class="bottom-strip" points="190,317 652,317 652,325 195,325" fill="var(--orange)"/>
  <polygon class="logo-panel" points="0,240 180,240 195,325 0,325" fill="var(--orange)"/>
  <text class="brand-name" fill="var(--white)" x="90" y="288" text-anchor="middle">Kemo IT Solutions</text>

  <g class="services">
    <polygon points="194,248 292,248 296,278 198,278" fill="var(--orange)"/>
    <text class="service-label" x="245" y="268" text-anchor="middle">IT Beratung</text>
    <polygon points="298,248 403,248 407,278 302,278" fill="var(--orange)"/>
    <text class="service-label" x="352" y="268" text-anchor="middle">IT Sicherheit</text>
    <polygon points="409,248 502,248 506,278 413,278" fill="var(--orange)"/>
    <text class="service-label" x="457" y="268" text-anchor="middle">IT Support</text>
    <polygon points="508,248 632,248 636,278 512,278" fill="var(--orange)"/>
    <text class="service-label" x="572" y="268" text-anchor="middle">IT Infrastruktur</text>
  </g>

  <polygon class="phone-bar" points="200,285 460,285 463,317 205,317" fill="var(--orange)"/>
  <text class="contact" fill="var(--white)" x="333" y="307" text-anchor="middle">Tel : +49 2351 / 38 72 14 0</text>
  <polygon class="web-bar" points="457,285 640,285 636,317 462,317" fill="var(--white)"/>
  <text class="contact" fill="var(--orange)" x="549" y="307" text-anchor="middle">www.kemo-it.de</text>
</svg>

</body>
</html>
```